Business Card Design Project

After recently finishing a design project for the company logo using markbazaar, it's now time for a business card. Attached to this is the logo.

The requirements for the business card are pretty straightforward:

- A clean, uncomplicated look
- Consistent usage of fonts
- Designs for both single sided and double sided cards
- A modern layout with preferably space to refer to social media accounts and/or downloadable vcards through a qr code
- consistent application of the company colour scheme: red/white. Hex codes for exact colour can be provided

Thanks!

```html
<!DOCTYPE html>
<html lang="en">
<head>
<meta charset="utf-8">
<title>Tall Kiln Recruiting – Business Card</title>
<link rel="stylesheet" href="https://fonts.googleapis.com/css2?family=Source+Sans+3:wght@400;600;700&display=swap">
<style>
  :root {
    --backdrop: #ebe8e4;
    --card: #ffffff;
    --ink: #231f20;
    --ink-soft: #3a3a3a;
    --grey: #8a8a8a;
    --rule: #555555;
    --brand-red: #e32227;
  }
  * { margin: 0; padding: 0; box-sizing: border-box; }
  html, body { width: 960px; height: 1200px; overflow: hidden; }
  body {
    position: relative;
    background: var(--backdrop);
    font-family: "Source Sans 3", sans-serif;
    color: var(--ink);
  }
  .card {
    position: absolute;
    width: 840px;
    height: 480px;
    background: var(--card);
    border-radius: 30px;
    box-shadow: 0 4px 10px rgba(0,0,0,0.12);
  }
  .card--front { left: 60px; top: 60px; }
  .card--back  { left: 55px; top: 637px; }

  .abs { position: absolute; white-space: nowrap; }

  /* front: wordmark */
  .wordmark-name {
    left: 88px; top: 24px;
    font-size: 56px; font-weight: 400; letter-spacing: -1px;
    color: var(--ink); line-height: 1;
  }
  .wordmark-tag {
    left: 90px; top: 88px;
    font-size: 30px; font-weight: 400; letter-spacing: 9px;
    text-transform: uppercase; color: var(--ink); line-height: 1;
  }

  /* front: contact block */
  .rule-vertical {
    left: 66px; top: 166px; width: 1.5px; height: 280px; background: var(--rule);
  }
  .rule-horizontal {
    left: 38px; top: 242px; width: 295px; height: 1.5px; background: var(--rule);
  }
  .person-name {
    left: 81px; top: 164px;
    font-size: 31px; font-weight: 700; color: var(--ink-soft); line-height: 1.2;
  }
  .person-role {
    left: 81px; top: 202px;
    font-size: 24px; color: var(--ink-soft); line-height: 1.2;
  }
  .contact-line {
    left: 81px; font-size: 23px; color: var(--ink-soft); line-height: 1.2;
  }
  .contact-phone { top: 256px; }
  .contact-email { top: 299px; }
  .contact-web   { top: 333px; }
  .contact-address { top: 378px; line-height: 32px; }
  .contact-icon { left: 40px; width: 14px; height: 14px; }
  .icon-phone { top: 266px; }
  .icon-email { top: 309px; }
  .icon-web   { top: 344px; }

  .brand-square--large {
    left: 525px; top: 165px; width: 220px; height: 220px;
    background: var(--brand-red);
  }

  /* back: lockup */
  .brand-square--small {
    left: 170px; top: 185px; width: 88px; height: 88px;
    background: var(--brand-red);
  }
  .lockup-name {
    left: 310px; top: 160px;
    font-size: 86px; font-weight: 400; letter-spacing: -1px;
    color: var(--ink); line-height: 1;
  }
  .lockup-tag {
    left: 262px; top: 262px;
    font-size: 48px; font-weight: 400; letter-spacing: 21px;
    text-transform: uppercase; color: var(--ink); line-height: 1;
  }
</style>
</head>
<body>

<section class="card card--front" aria-label="Card front">
  <div class="abs wordmark-name">Tall Kiln</div>
  <div class="abs wordmark-tag">Recruiting</div>

  <div class="abs rule-vertical"></div>
  <div class="abs rule-horizontal"></div>

  <div class="abs person-name">Your Name</div>
  <div class="abs person-role">Designation</div>

  <svg class="abs contact-icon icon-phone" viewBox="0 0 14 14" aria-hidden="true">
    <path d="M1 5 C1 2 13 2 13 5 L10 5.5 L9.5 4 L4.5 4 L4 5.5 Z" fill="var(--ink-soft)"/>
    <path d="M3.5 6.5 L10.5 6.5 L12 12 L2 12 Z" fill="var(--ink-soft)"/>
  </svg>
  <div class="abs contact-line contact-phone">123-123-1234</div>

  <svg class="abs contact-icon icon-email" viewBox="0 0 14 14" aria-hidden="true">
    <rect x="1" y="3" width="12" height="8" fill="none" stroke="var(--ink-soft)" stroke-width="1.4"/>
    <path d="M1 3 L7 8 L13 3" fill="none" stroke="var(--ink-soft)" stroke-width="1.4"/>
  </svg>
  <div class="abs contact-line contact-email">info@tallkiln.com</div>

  <svg class="abs contact-icon icon-web" viewBox="0 0 14 14" aria-hidden="true">
    <circle cx="7" cy="7" r="6" fill="var(--ink-soft)"/>
    <path d="M1 7 H13 M7 1 C4 4 4 10 7 13 M7 1 C10 4 10 10 7 13" fill="none" stroke="#fff" stroke-width="0.8"/>
  </svg>
  <div class="abs contact-line contact-web">www.tallkiln.com</div>

  <div class="abs contact-line contact-address">1234, Street Name, City<br>District, Country Code.</div>

  <div class="abs brand-square--large"></div>
</section>

<section class="card card--back" aria-label="Card back">
  <div class="abs brand-square--small"></div>
  <div class="abs lockup-name">Tall Kiln</div>
  <div class="abs lockup-tag">Recruiting</div>
</section>

</body>
</html>
```